Veranix - Solution provider in business consulting

Veranix is a swiss based company providing solutions for developing markets. The business covers various fields of business consulting, such as supply chain, product costs, quality management and manufacturing management. The Business operates in a efficient, straight and solution oriented manner.
The final design should communicate these characteristics. Asian people as well as as western people shall identify the qualities of the company at first sight.
The customer needs business cards with a simple view but an recognizable design, printed in high quality. Engraved elements such as the globe or simple words are possible.
Available colors are: (RAL)
102/102/102
51/102/102
153/204/153
255/102/51
Font: Calibri

```html
<!DOCTYPE html>
<html lang="en">
<head>
<meta charset="utf-8">
<title>Veranix Business Card</title>
<link href="https://fonts.googleapis.com/css2?family=Carlito:wght@400;700&display=swap" rel="stylesheet">
<style>
  :root {
    --backdrop: #151515;
    --card-white: #ffffff;
    --brand-grey: #666666;
    --ink-dark: #222222;
    --ink-mid: #4d4d4d;
    --ink-light: #ffffff;
  }
  html, body {
    margin: 0;
    padding: 0;
    width: 1200px;
    height: 900px;
    overflow: hidden;
    background: var(--backdrop);
    font-family: "Carlito", "Calibri", sans-serif;
  }
  .canvas {
    position: relative;
    width: 1200px;
    height: 900px;
  }
  .card {
    position: absolute;
    top: 170px;
    width: 347px;
    height: 561px;
    box-sizing: border-box;
  }
  .card--front {
    left: 259px;
    background: var(--card-white);
  }
  .card--back {
    left: 631px;
    background: var(--brand-grey);
  }
  .card__tab {
    position: absolute;
    left: 101px;
    width: 144px;
    height: 30px;
    background: var(--brand-grey);
  }
  .card__tab--top { top: 0; }
  .card__tab--bottom { bottom: 0; }

  .wordmark {
    position: absolute;
    left: 0;
    right: 0;
    display: flex;
    justify-content: center;
    align-items: center;
    gap: 12px;
    font-size: 50px;
    font-weight: 400;
    letter-spacing: 1px;
    line-height: 1;
  }
  .wordmark__dot {
    width: 14px;
    height: 14px;
    border-radius: 50%;
    background: currentColor;
  }
  .card--front .wordmark {
    top: 135px;
    color: var(--brand-grey);
  }
  .card--back .wordmark {
    top: 402px;
    color: var(--ink-light);
  }

  .holder {
    position: absolute;
    top: 262px;
    left: 0;
    right: 0;
    text-align: center;
  }
  .holder__name {
    margin: 0;
    font-size: 21px;
    font-weight: 700;
    color: var(--ink-dark);
    line-height: 1.1;
  }
  .holder__role {
    margin: 2px 0 0;
    font-size: 15px;
    color: var(--ink-mid);
  }

  .contacts {
    position: absolute;
    top: 323px;
    left: 0;
    right: 0;
    margin: 0;
    padding: 0;
    list-style: none;
    text-align: center;
  }
  .contacts__item {
    display: flex;
    justify-content: center;
    align-items: center;
    gap: 9px;
    height: 23px;
    font-size: 16px;
    color: var(--ink-mid);
  }
  .contacts__icon {
    width: 11px;
    height: 11px;
    fill: var(--ink-mid);
    flex: none;
  }

  .address {
    position: absolute;
    top: 421px;
    left: 0;
    right: 0;
    margin: 0;
    text-align: center;
    font-style: normal;
    font-size: 16px;
    line-height: 21px;
    color: var(--ink-mid);
  }
</style>
</head>
<body>
<main class="canvas">

  <section class="card card--front" aria-label="Business card front">
    <div class="card__tab card__tab--top"></div>

    <div class="wordmark"><span>Veranix</span><span class="wordmark__dot"></span></div>

    <div class="holder">
      <p class="holder__name">Marco Keller</p>
      <p class="holder__role">CEO</p>
    </div>

    <ul class="contacts">
      <li class="contacts__item">
        <svg class="contacts__icon" viewBox="0 0 12 12" aria-hidden="true"><path d="M3 0h6a1 1 0 0 1 1 1v10a1 1 0 0 1-1 1H3a1 1 0 0 1-1-1V1a1 1 0 0 1 1-1zm0 1.5v7.5h6V1.5zM6 9.6a.8.8 0 1 0 0 1.6.8.8 0 0 0 0-1.6z"/></svg>
        <span>+41 79 555 0182</span>
      </li>
      <li class="contacts__item">
        <svg class="contacts__icon" viewBox="0 0 12 12" aria-hidden="true"><path d="M2.4 0.5l2 2.3-1.1 1.5c.8 1.7 2.1 3 3.8 3.8l1.5-1.1 2.3 2-1.2 2C5 10.8 1.2 7 .5 1.7z"/></svg>
        <span>+41 71 555 0147</span>
      </li>
      <li class="contacts__item">
        <svg class="contacts__icon" viewBox="0 0 12 12" aria-hidden="true"><path d="M0 2h12v8H0zm1 1v.4l5 3.2 5-3.2V3zm0 1.6V9h10V4.6L6 7.8z"/></svg>
        <span>marco.keller@veranix.ch</span>
      </li>
      <li class="contacts__item">
        <svg class="contacts__icon" viewBox="0 0 12 12" aria-hidden="true"><circle cx="6" cy="6" r="5.5"/><path d="M6 .5v11M.5 6h11M6 .5c-2.2 2.8-2.2 8.2 0 11M6 .5c2.2 2.8 2.2 8.2 0 11" stroke="#fff" stroke-width=".8" fill="none"/></svg>
        <span>www.veranix.ch</span>
      </li>
    </ul>

    <address class="address">
      Veranix GmbH Lindenweg 14<br>
      9246 Niederau Switzerland
    </address>

    <div class="card__tab card__tab--bottom"></div>
  </section>

  <section class="card card--back" aria-label="Business card back">
    <div class="wordmark"><span>Veranix</span><span class="wordmark__dot"></span></div>
  </section>

</main>
</body>
</html>
```